Redesign of business card for Cedar Ridge Mechanical

We are looking for a new design for our business cards for Cedar Ridge Mechanical. We are a plumbing & HVAC construction company, operating on the West Coast of Canada and USA. Logo attached.
Industry/Entity Type
Construction - Plumbing & HVAC
Contact Information for Business Card
Name, address, phone numbers, email, website address
Look and feel
Each slider illustrates characteristics of the customer's brand and the style your logo design should communicate.

```html
<!DOCTYPE html>
<html lang="en">
<head>
<meta charset="utf-8">
<title>Cedar Ridge Mechanical – Business Card</title>
<link rel="stylesheet" href="https://fonts.googleapis.com/css2?family=Montserrat:wght@400;700;800&display=swap">
<style>
  :root {
    --ink: #0b0b0b;
    --paper: #ffffff;
    --stripe: #8f8f8f;
    --backdrop: #d9d9d9;
    --soft-text: #e6e6e6;
  }
  * { box-sizing: border-box; margin: 0; padding: 0; }
  html, body { width: 1200px; height: 913px; overflow: hidden; }
  body {
    background: var(--backdrop);
    font-family: "Montserrat", Arial, sans-serif;
    position: relative;
  }
  .card {
    position: absolute;
    width: 520px;
    height: 298px;
    border-radius: 18px;
    background: var(--paper);
    overflow: hidden;
    box-shadow: 0 10px 28px rgba(0,0,0,.18);
  }
  .card-front { left: 120px; top: 110px; }
  .card-back  { left: 560px; top: 505px; }

  .brand {
    position: absolute;
    display: flex;
    align-items: center;
    gap: 14px;
    color: var(--ink);
    font-weight: 800;
    text-transform: uppercase;
    letter-spacing: .5px;
  }
  .brand-mark {
    border: 4px solid var(--ink);
    border-radius: 8px;
    flex: none;
  }
  .card-front .brand { left: 0; right: 0; top: 0; bottom: 0; justify-content: center; font-size: 24px; }
  .card-front .brand-mark { width: 58px; height: 58px; }
  .card-front .brand-name { line-height: 1.15; }

  .card-back .brand { right: 26px; top: 28px; font-size: 14px; gap: 10px; }
  .card-back .brand-mark { width: 38px; height: 38px; border-width: 3px; border-radius: 6px; }
  .card-back .brand-name { line-height: 1.2; }

  .wave { position: absolute; inset: 0; width: 100%; height: 100%; }

  .holder {
    position: absolute;
    left: 34px;
    top: 168px;
    color: var(--paper);
  }
  .holder-name { font-weight: 800; font-size: 20px; letter-spacing: .5px; }
  .holder-role { font-weight: 400; font-size: 12.5px; color: var(--soft-text); margin-top: 2px; }

  .contact-list {
    position: absolute;
    left: 34px;
    top: 222px;
    list-style: none;
    color: var(--paper);
    font-size: 12.5px;
  }
  .contact-list li { display: flex; align-items: center; gap: 8px; height: 20px; }
  .contact-list svg { width: 12px; height: 12px; flex: none; }

  .address {
    position: absolute;
    right: 26px;
    top: 128px;
    text-align: right;
    color: var(--paper);
    font-size: 12.5px;
    line-height: 1.5;
  }
</style>
</head>
<body>

  <section class="card card-front" aria-label="Card front">
    <div class="brand">
      <span class="brand-mark"></span>
      <span class="brand-name">Cedar Ridge<br>Mechanical</span>
    </div>
  </section>

  <section class="card card-back" aria-label="Card back">
    <svg class="wave" viewBox="0 0 520 298" preserveAspectRatio="none" aria-hidden="true">
      <path d="M0,138 C110,92 200,116 300,112 C410,108 470,72 520,8 L520,24 C470,88 410,122 300,126 C200,130 110,108 0,152 Z" fill="var(--stripe)"/>
      <path d="M0,162 C110,118 200,138 300,134 C410,130 470,96 520,30 L520,298 L0,298 Z" fill="var(--ink)"/>
    </svg>

    <div class="brand">
      <span class="brand-mark"></span>
      <span class="brand-name">Cedar Ridge<br>Mechanical</span>
    </div>

    <div class="address">Your address, City<br>State, Zip 1234</div>

    <div class="holder">
      <p class="holder-name">DANIEL HART</p>
      <p class="holder-role">Managing Director</p>
    </div>

    <ul class="contact-list">
      <li>
        <svg viewBox="0 0 24 24" aria-hidden="true"><path fill="#fff" d="M6.6 10.8a15.1 15.1 0 0 0 6.6 6.6l2.2-2.2c.3-.3.7-.4 1-.2 1.1.4 2.3.6 3.6.6.6 0 1 .4 1 1V20c0 .6-.4 1-1 1C10.6 21 3 13.4 3 4c0-.6.4-1 1-1h3.5c.6 0 1 .4 1 1 0 1.3.2 2.5.6 3.6.1.3 0 .7-.2 1z"/></svg>
        <span>123 456 789</span>
      </li>
      <li>
        <svg viewBox="0 0 24 24" aria-hidden="true"><rect x="2" y="5" width="20" height="14" rx="2" fill="#fff"/><path d="M3 6l9 7 9-7" fill="none" stroke="#0b0b0b" stroke-width="2"/></svg>
        <span>info@yourgmail.com</span>
      </li>
      <li>
        <svg viewBox="0 0 24 24" aria-hidden="true"><circle cx="12" cy="12" r="10" fill="none" stroke="#fff" stroke-width="2"/><ellipse cx="12" cy="12" rx="4.5" ry="10" fill="none" stroke="#fff" stroke-width="1.6"/><path d="M2 12h20" stroke="#fff" stroke-width="1.6"/></svg>
        <span>www.yourwebsite.com</span>
      </li>
    </ul>
  </section>

</body>
</html>
```